Spirits Bottle Label-Brand Name Reed & Barrow

Design a spirits bottle label per specifications outlined. Label size Front 3.875x 4.5,Back 2x4, topper 1x5.7. Must have established 2020, 40% Alcohol by volume. 40 proof. Sherry Cask Settled. Bottle # 1 of 1320. Caribbean Rum. Trademark logo must be on the label. Back of label has to have all the information outlined in photo. Topper & Front of the label the designer can you his creativity. Color scheme is negotiable and designers can be creative.

Target Market(s)

Adults aged 21 with an appealing appearance that caters to a young professionals and seasoned adults

Font styles to use
Sans Serif

Colors
886aae
33b8a4
33a6d7

Requirements
Must have
• -Reed & Barrow Trademark Logo which is attached.
-Caribbean Rum
-40% Alcohol By Volume
-80 Proof
-Sherry Cask Settled
-Established 2020

```html
<!DOCTYPE html>
<html lang="en">
<head>
<meta charset="utf-8">
<title>Reed &amp; Barrow Caribbean Rum Labels</title>
<link href="https://fonts.googleapis.com/css2?family=Oswald:wght@500;700&family=Libre+Baskerville:wght@400;700&family=Playball&family=Roboto:wght@400;700&display=swap" rel="stylesheet">
<style>
  :root{
    --page:#ffffff;
    --paper:#f1efe1;
    --ink:#2b2b2b;
    --teal:#7cc0ad;
    --teal-script:#72c3ab;
    --light:#f4f4ee;
  }
  *{margin:0;padding:0;box-sizing:border-box}
  html,body{width:1200px;height:1200px;overflow:hidden;background:var(--page)}
  .canvas{position:relative;width:1200px;height:1200px}

  /* Topper */
  .topper{position:absolute;left:70px;top:330px;width:62px;height:420px;background:var(--paper);
    box-shadow:0 0 0 1px #e2e0d2}
  .topper__rule{position:absolute;top:14px;bottom:14px;width:3px;background:var(--ink)}
  .topper__rule--left{left:10px}
  .topper__rule--right{right:10px}
  .topper__name{position:absolute;left:50%;top:150px;transform:translate(-50%,-50%) rotate(-90deg);
    font:700 34px/1 'Oswald',sans-serif;color:var(--ink);white-space:nowrap;letter-spacing:.5px}
  .topper__art{position:absolute;left:17px;bottom:24px;width:28px;height:70px;
    background:linear-gradient(#4a4a4a,#2b2b2b);opacity:.85}

  /* Front label */
  .front{position:absolute;left:170px;top:300px;width:510px;height:570px;background:var(--paper);overflow:hidden}
  .front__frame{position:absolute;inset:8px;border:2px solid var(--teal)}
  .front__scene{position:absolute;left:10px;right:10px;top:10px;height:460px;
    background:radial-gradient(ellipse at 50% 55%,rgba(200,205,192,.55),rgba(241,239,225,0) 70%),
               linear-gradient(90deg,rgba(205,210,198,.6),rgba(241,239,225,0) 35%,rgba(241,239,225,0) 65%,rgba(205,210,198,.5))}
  .front__mark{position:absolute;left:50%;top:28px;width:100px;height:100px;margin-left:-50px;border-radius:50%;background:var(--ink)}
  .front__name{position:absolute;left:0;right:0;top:162px;text-align:center;white-space:nowrap;
    font:700 80px/1 'Oswald',sans-serif;color:var(--ink);letter-spacing:-1px;transform:scaleX(.84)}
  .front__arc{position:absolute;left:0;top:256px;width:510px;height:50px}
  .front__arc text{font:400 20px 'Libre Baskerville',serif;fill:var(--ink);letter-spacing:5px}
  .dots{display:flex;justify-content:center;align-items:center;gap:7px}
  .dots span{display:block;border-radius:50%;background:var(--ink)}
  .front__dots{position:absolute;left:0;right:0;top:304px}
  .front__type{position:absolute;left:0;right:0;top:316px;text-align:center;
    font:400 56px/1.1 'Playball',cursive;color:var(--teal-script)}
  .front__batch{position:absolute;left:0;right:0;top:390px;text-align:center;
    font:400 20px/1 'Libre Baskerville',serif;letter-spacing:4px;color:#3a3a3a}
  .front__proof{position:absolute;left:0;right:0;top:416px;display:flex;justify-content:center;align-items:center;gap:14px;color:var(--ink)}
  .front__proof .side{font:400 18px 'Libre Baskerville',serif;letter-spacing:2px;border-top:2px solid var(--teal);border-bottom:2px solid var(--teal);padding:1px 0}
  .front__proof .num{font:700 38px/1 'Libre Baskerville',serif}
  .front__proof-word{position:absolute;left:0;right:0;top:458px;text-align:center;font:400 14px/1 'Libre Baskerville',serif;letter-spacing:2px;color:var(--ink)}
  .front__band{position:absolute;left:0;top:455px;width:510px;height:115px}
  .band-text{font:700 19px 'Roboto',sans-serif;fill:var(--ink);letter-spacing:2px}
  .front__meta{position:absolute;font:400 13px/1.9 'Roboto',sans-serif;color:var(--light);letter-spacing:.5px}
  .front__meta--left{left:30px;top:484px}
  .front__meta--right{right:30px;top:484px;text-align:center}
  .front__bottle-no{display:block;margin-top:4px;width:96px;height:28px;border-radius:6px;background:var(--paper);
    color:#555;font:italic 400 13px/28px 'Roboto',sans-serif}
  .front__dots--low{position:absolute;left:0;right:0;top:534px}
  .front__dots--low span{background:var(--light)}

  /* Back label */
  .back{position:absolute;left:705px;top:470px;width:450px;height:262px;background:var(--paper);
    border:3px solid var(--teal);border-radius:8px;color:var(--ink)}
  .back__col{position:absolute;left:14px;top:12px;width:282px}
  .back__lead{text-align:center;font:500 17px/1.2 'Oswald',sans-serif;letter-spacing:1px}
  .back__script{text-align:center;font:400 19px/1.2 'Playball',cursive;color:var(--teal-script)}
  .back__source{margin-top:6px;padding:3px 0;border-top:1px solid var(--ink);border-bottom:1px solid var(--ink);
    text-align:center;font:400 12px 'Libre Baskerville',serif;letter-spacing:2px;white-space:nowrap}
  .back__maker{display:flex;gap:8px;align-items:flex-start;margin:10px 0 8px}
  .back__maker .ring{flex:none;width:28px;height:28px;border-radius:50%;border:2px solid var(--ink)}
  .back__maker p{font:400 11.5px/1.35 'Libre Baskerville',serif;letter-spacing:.5px}
  .back__warning{font:400 8.4px/1.35 'Libre Baskerville',serif;text-align:justify}
  .back__name{position:absolute;right:8px;top:30px;width:140px;text-align:center;white-space:nowrap;
    font:700 24px/1 'Oswald',sans-serif;letter-spacing:-.3px;transform:scaleX(.88)}
  .back__art{position:absolute;right:14px;top:70px;width:128px;height:64px;
    background:linear-gradient(#8b8b8b,#2b2b2b)}
</style>
</head>
<body>
<main class="canvas">

  <section class="topper" aria-label="Neck topper">
    <span class="topper__rule topper__rule--left"></span>
    <span class="topper__rule topper__rule--right"></span>
    <span class="topper__name">REED &amp; BARROW</span>
    <div class="topper__art" role="img" aria-label="Small sugar cane drawing"></div>
  </section>

  <section class="front" aria-label="Front label">
    <div class="front__scene" role="img" aria-label="Faint etched scene of palms and a sailing ship in a bay"></div>
    <div class="front__frame"></div>
    <span class="front__mark" aria-hidden="true"></span>
    <h1 class="front__name">REED &amp; BARROW</h1>
    <svg class="front__arc" viewBox="0 0 510 50" aria-label="Authentic">
      <path id="arcTop" d="M170 42 Q255 14 340 42" fill="none"/>
      <text><textPath href="#arcTop" startOffset="50%" text-anchor="middle">AUTHENTIC</textPath></text>
    </svg>
    <div class="dots front__dots"><span style="width:5px;height:5px"></span><span style="width:6px;height:6px"></span><span style="width:9px;height:9px"></span><span style="width:6px;height:6px"></span><span style="width:5px;height:5px"></span></div>
    <p class="front__type">Caribbean Rum</p>
    <p class="front__batch">SMALL BATCH CRAFTED</p>
    <div class="front__proof"><span class="side">EST.</span><span class="num">80</span><span class="side">2020</span></div>
    <p class="front__proof-word">PROOF</p>
    <svg class="front__band" viewBox="0 0 510 115" aria-label="Sherry cask aged">
      <path d="M10 15 H140 Q255 115 370 15 H500 V107 H10 Z" fill="var(--teal)"/>
      <path id="arcLow" d="M150 8 Q255 82 360 8" fill="none"/>
      <text class="band-text"><textPath href="#arcLow" startOffset="50%" text-anchor="middle">SHERRY CASK AGED</textPath></text>
    </svg>
    <div class="front__meta front__meta--left">750 ML.<br>ALC. BY VOL. 40%</div>
    <div class="front__meta front__meta--right">BOTTLE NO.<span class="front__bottle-no">0001 / 1320</span></div>
    <div class="dots front__dots--low"><span style="width:4px;height:4px"></span><span style="width:7px;height:7px"></span><span style="width:11px;height:11px"></span><span style="width:7px;height:7px"></span><span style="width:4px;height:4px"></span></div>
  </section>

  <section class="back" aria-label="Back label">
    <div class="back__col">
      <p class="back__lead">CELEBRATE LIFE WITH FAMILY,</p>
      <p class="back__script">Old &amp; New Friends</p>
      <p class="back__source">DISTILLED FROM SUGAR CANE</p>
      <div class="back__maker"><span class="ring"></span>
        <p>DISTILLED AND BOTTLED BY<br>REED &amp; BARROW DISTILLERY<br>MILLBROOK, NC &nbsp;27000</p></div>
      <p class="back__warning">GOVERNMENT WARNING: (1) ACCORDING TO THE SURGEON GENERAL, WOMEN SHOULD NOT DRINK ALCOHOLIC BEVERAGES DURING PREGNANCY BECAUSE OF THE RISK OF BIRTH DEFECTS. (2) CONSUMPTION OF ALCOHOLIC BEVERAGES IMPAIRS YOUR ABILITY TO DRIVE A CAR OR OPERATE MACHINERY, AND MAY CAUSE HEALTH PROBLEMS.</p>
    </div>
    <p class="back__name">REED &amp; BARROW</p>
    <div class="back__art" role="img" aria-label="Row of sugar cane stalks drawing"></div>
  </section>

</main>
</body>
</html>
```